Web site for a company that sells Gadget Arcade machines

We need a website that is an online shopping experience for a Store that sells pinball machines and accessories. The name of the store is called "Gadget Arcade." The store it self has a showroom, but we would also like to have an Internet e-commerce presence. We pinball machines made by Vexler pinball. You can visit their website and see their current list of machines as well as their website for the machines that we are going to carry in our store. Their website is Vexlerpinball.com. I am able to use their machine photos as well as their machine brochure PDF files. I am also able to use their logo on my website two list it as a Vexler Authorized Dealer.
This website design needs to be funky, fun, very technologically oriented and modern. The people buying machines our spending anywhere between $5000 and $15,000 on one machine. These Are high-end buyers who are also usually fairly tech savvy or at least enjoy technology and graphics.
Attachments: I have attached photographs of some of my own machines which may be used in the website. I've also attached some downloaded files from Vexler pinball.com as well as some of their PDF files for brochures. I will carry all of their current models they have listed under games. Not the archived games. I have included one of their machines called Thunderwolf Limited edition in my photograph attachments. The rest of the photos are just random pictures that I have taken myself and maybe used to build the site. Lastly I have attached my logo which I am not super crazy about so I will also be posting a contest to redesign this logo. Tons more of my own pinball photos are available.
I would like for people to be able to purchase machines and accessories from the website, but also inform them to our actual showroom.
Updates
Project Deadline Extended Reason: Hello. We have extended five days due to some complications during the construction of our actual building. We were unable to participate in this web design during this time and so unfortunately were not able give feedback appropriately. We are back on track and will provide feedback to the designers who have designed up until this point. We will still be interested in seeing new submissions, however; this extension will give us a chance to provide feedback and coordinate the website appropriately. Thank you so much for your submissions and your patience!!!!Gadget Arcade Added Friday, April 21, 2017
Target Market(s)
Target market is 16 to 75. Techy individuals to enjoy gaming technology video animation and Vegas style twinkle
Industry/Entity Type
It Company
Coding
Coded - Design and coding required
Number of Pages Required
3 page
Font styles to use
Look and feel
Each slider illustrates characteristics of the customer's brand and the style your logo design should communicate.

```html
<!DOCTYPE html>
<html lang="en">
<head>
<meta charset="utf-8">
<title>Gadget Arcade</title>
<link href="https://fonts.googleapis.com/css2?family=Nunito:wght@400;600&family=Oswald:wght@400;500&family=Open+Sans:wght@600&display=swap" rel="stylesheet">
<style>
  :root{
    --bg-dark:#0d0b0c;
    --bg-warm:#2a1410;
    --orange:#e8730f;
    --nav-top:#6a6a6a;
    --nav-bottom:#2b2b2b;
    --white:#ffffff;
    --label-band:#3a3a3a;
    --footer:#121212;
    --cabinet:#4b3f94;
    --cabinet-deep:#2b2466;
    --cabinet-gold:#c9a443;
  }
  *{box-sizing:border-box;margin:0;padding:0}
  html,body{width:1178px;height:1200px;overflow:hidden}
  body{
    position:relative;
    font-family:"Nunito",sans-serif;color:var(--white);
    background:
      radial-gradient(ellipse 400px 300px at 15% 20%, rgba(120,20,30,.45), transparent 70%),
      radial-gradient(ellipse 500px 300px at 85% 30%, rgba(90,20,80,.4), transparent 70%),
      radial-gradient(ellipse 700px 260px at 50% 90%, rgba(110,70,20,.35), transparent 70%),
      linear-gradient(180deg, var(--bg-dark), var(--bg-warm) 60%, #1a1512);
  }
  .phone{position:absolute;left:90px;top:35px;display:flex;align-items:center;gap:8px;font-size:19px;font-weight:600}
  .search{position:absolute;left:855px;top:31px;width:230px;height:31px;border:1px solid #cfcfcf;border-radius:16px;display:flex;align-items:center;justify-content:space-between;padding:0 12px 0 15px;font-size:14px}
  .nav{position:absolute;left:88px;top:89px;width:1005px;height:54px;background:linear-gradient(180deg,var(--nav-top),var(--nav-bottom))}
  .nav a{position:absolute;top:0;height:54px;line-height:54px;transform:translateX(-50%);color:var(--white);text-decoration:none;font-size:15px}
  .nav a.active{background:var(--orange);width:97px;text-align:center;transform:none;left:0}
  .brand{position:absolute;left:499px;top:24px;width:180px;z-index:3;display:flex;flex-direction:column;align-items:center}
  .brand-dot{width:60px;height:60px;border-radius:50%;background:#b9b9b9}
  .brand-name{margin-top:18px;font-size:16px;font-weight:600;color:var(--white);line-height:20px}
  .hero{position:absolute;left:88px;top:143px;width:1005px;height:506px;border:1px solid #ddd;
    background:
      radial-gradient(ellipse 180px 200px at 60% 45%, rgba(60,180,80,.75), transparent 70%),
      radial-gradient(ellipse 300px 250px at 85% 60%, rgba(230,40,160,.55), transparent 70%),
      radial-gradient(ellipse 300px 300px at 20% 40%, rgba(160,160,190,.55), transparent 70%),
      linear-gradient(135deg,#2a2070,#4a2f9a 45%,#6a2a8a 70%,#3a1a50)}
  .hero-caption{position:absolute;left:20px;top:269px;width:386px;height:191px;background:rgba(30,30,30,.72);padding:20px 0 0 26px}
  .hero-caption h1{font-family:"Oswald",sans-serif;font-weight:400;font-size:45px;line-height:1;letter-spacing:-1.5px;white-space:nowrap}
  .hero-caption p{font-family:"Oswald",sans-serif;font-size:20px;line-height:29px;letter-spacing:-.6px;margin-top:6px;white-space:nowrap}
  .btn-buy{display:inline-block;margin-top:7px;background:var(--orange);color:var(--white);font-size:16px;padding:0 21px;height:40px;line-height:40px;border-radius:20px;text-decoration:none}
  .machines{position:absolute;left:88px;top:660px;display:flex;gap:8px}
  .machine{width:194px;height:173px}
  .machine-photo{height:142px;
    background:
      radial-gradient(ellipse 26px 20px at 50% 64%, rgba(201,164,67,.55), transparent 80%),
      radial-gradient(ellipse 38px 62px at 50% 52%, var(--cabinet) 0%, rgba(43,36,102,.75) 45%, transparent 85%),
      radial-gradient(ellipse at center,#ffffff 35%,#d6d6d6 100%)}
  .machine-photo.wide{
    background:
      radial-gradient(ellipse 30px 20px at 50% 60%, rgba(201,164,67,.55), transparent 80%),
      radial-gradient(ellipse 52px 58px at 50% 52%, var(--cabinet) 0%, rgba(43,36,102,.75) 45%, transparent 85%),
      radial-gradient(ellipse at center,#ffffff 35%,#d6d6d6 100%)}
  .machine-label{height:31px;background:var(--label-band);display:flex;align-items:center;justify-content:center;gap:7px;font-size:15px}
  .welcome{position:absolute;left:0;top:885px;width:1178px;text-align:center}
  .welcome h2{font-family:"Open Sans",sans-serif;font-weight:600;font-size:29px;letter-spacing:.3px}
  .welcome p{width:890px;margin:8px auto 0;font-size:15.5px;line-height:22.5px}
  .footer{position:absolute;left:0;top:1041px;width:1178px;height:159px;background:var(--footer);text-align:center}
  .footer-links{margin-top:40px;font-size:13px;display:flex;justify-content:center;gap:11px}
  .social{display:flex;justify-content:center;gap:8px;margin-top:14px}
  .social span{width:26px;height:26px;border:1.5px solid #ddd;border-radius:50%;display:flex;align-items:center;justify-content:center}
  .copyright{margin-top:12px;font-size:13px}
</style>
</head>
<body>
  <div class="phone">
    <svg width="16" height="16" viewBox="0 0 16 16"><rect width="16" height="16" rx="3" fill="#fff"/><path d="M5 3.5l1.6 2-1 1.2c.6 1.4 1.6 2.4 3 3l1.2-1 2 1.6-1 1.9c-3.4-.2-6.5-3.3-6.7-6.7z" fill="#111"/></svg>
    555 013 0199
  </div>
  <div class="search">Search
    <svg width="14" height="14" viewBox="0 0 14 14"><circle cx="6" cy="6" r="4.3" fill="none" stroke="#fff" stroke-width="2"/><path d="M9 9l3.5 3.5" stroke="#fff" stroke-width="2.2" stroke-linecap="round"/></svg>
  </div>

  <nav class="nav">
    <a class="active" href="#">HOME</a>
    <a href="#" style="left:155px">ABOUT US</a>
    <a href="#" style="left:260px">GAME</a>
    <a href="#" style="left:363px">SERVICES</a>
    <a href="#" style="left:627px">PIN BALL</a>
    <a href="#" style="left:739px">SUPPORT</a>
    <a href="#" style="left:840px">BLOG</a>
    <a href="#" style="left:944px">CONTACTS</a>
  </nav>
  <div class="brand"><div class="brand-dot"></div><div class="brand-name">Gadget Arcade</div></div>

  <section class="hero" role="img" aria-label="Close-up photo of a lit pinball playfield with a figure, ramps and purple lightning artwork">
    <div class="hero-caption">
      <h1>PINBALL MACHINES</h1>
      <p>Buying machines our spending anywhere<br>Between $5000 and $15,000 on one machine</p>
      <a class="btn-buy" href="#">BUY NOW</a>
    </div>
  </section>

  <section class="machines">
    <div class="machine"><div class="machine-photo" role="img" aria-label="Purple pinball machine cabinet, front view"></div><div class="machine-label">MACHINES <svg width="14" height="14" viewBox="0 0 14 14"><circle cx="7" cy="7" r="7" fill="#fff"/><path d="M5.5 4l3 3-3 3" fill="none" stroke="#333" stroke-width="2"/></svg></div></div>
    <div class="machine"><div class="machine-photo wide" role="img" aria-label="Purple pinball machine cabinet, angled view"></div><div class="machine-label">MACHINES <svg width="14" height="14" viewBox="0 0 14 14"><circle cx="7" cy="7" r="7" fill="#fff"/><path d="M5.5 4l3 3-3 3" fill="none" stroke="#333" stroke-width="2"/></svg></div></div>
    <div class="machine"><div class="machine-photo" role="img" aria-label="Purple pinball machine cabinet, front view"></div><div class="machine-label">MACHINES <svg width="14" height="14" viewBox="0 0 14 14"><circle cx="7" cy="7" r="7" fill="#fff"/><path d="M5.5 4l3 3-3 3" fill="none" stroke="#333" stroke-width="2"/></svg></div></div>
    <div class="machine"><div class="machine-photo wide" role="img" aria-label="Purple pinball machine cabinet, side angle"></div><div class="machine-label">MACHINES <svg width="14" height="14" viewBox="0 0 14 14"><circle cx="7" cy="7" r="7" fill="#fff"/><path d="M5.5 4l3 3-3 3" fill="none" stroke="#333" stroke-width="2"/></svg></div></div>
    <div class="machine"><div class="machine-photo wide" role="img" aria-label="Purple pinball machine cabinet, angled view"></div><div class="machine-label">MACHINES <svg width="14" height="14" viewBox="0 0 14 14"><circle cx="7" cy="7" r="7" fill="#fff"/><path d="M5.5 4l3 3-3 3" fill="none" stroke="#333" stroke-width="2"/></svg></div></div>
  </section>

  <section class="welcome">
    <h2>WELCOME TO GADGET ARCADE</h2>
    <p>It is a long established fact that a reader will be distracted by the readable content of a page when looking at its layout. The point of using Lorem Ipsum is that it has a more-or-less normal distribution of letters, as opposed to using 'Content here, content here', making it look like readable English. Many desktop publishing packages and web page editors now use Lorem Ipsum</p>
  </section>

  <footer class="footer">
    <div class="footer-links"><span>ABOUT</span><span>|</span><span>PRIVACY</span><span>|</span><span>TERMS</span><span>|</span><span>LEGAL</span><span>|</span><span>CONTACT</span></div>
    <div class="social">
      <span aria-label="Link"><svg width="12" height="12" viewBox="0 0 12 12"><path d="M5 7l2-2M4.2 5.6L3 6.8a1.8 1.8 0 002.5 2.5l1.2-1.2M7.8 6.4L9 5.2a1.8 1.8 0 00-2.5-2.5L5.3 3.9" fill="none" stroke="#fff" stroke-width="1.2" stroke-linecap="round"/></svg></span>
      <span aria-label="Chat"><svg width="12" height="12" viewBox="0 0 12 12"><path d="M1.5 2h9v6H5L2.5 10V8h-1z" fill="none" stroke="#fff" stroke-width="1.1" stroke-linejoin="round"/></svg></span>
      <span aria-label="Share"><svg width="12" height="12" viewBox="0 0 12 12"><circle cx="9" cy="2.5" r="1.5" fill="#fff"/><circle cx="3" cy="6" r="1.5" fill="#fff"/><circle cx="9" cy="9.5" r="1.5" fill="#fff"/><path d="M9 2.5L3 6l6 3.5" fill="none" stroke="#fff" stroke-width="1"/></svg></span>
      <span aria-label="Favourite"><svg width="12" height="12" viewBox="0 0 12 12"><path d="M6 10.3L1.8 6.2a2.4 2.4 0 013.5-3.3L6 3.6l.7-.7a2.4 2.4 0 013.5 3.3z" fill="none" stroke="#fff" stroke-width="1.1"/></svg></span>
      <span aria-label="Rating"><svg width="12" height="12" viewBox="0 0 12 12"><path d="M6 1l1.5 3.2 3.5.4-2.6 2.4.7 3.5L6 8.8 2.9 10.5l.7-3.5L1 4.6l3.5-.4z" fill="none" stroke="#fff" stroke-width="1" stroke-linejoin="round"/></svg></span>
      <span aria-label="Email"><svg width="12" height="9" viewBox="0 0 12 9"><rect x=".5" y=".5" width="11" height="8" fill="none" stroke="#fff"/><path d="M.5 .5l5.5 4.5 5.5-4.5" fill="none" stroke="#fff"/></svg></span>
    </div>
    <div class="copyright">Copyright © 2017&nbsp; All Rights Reserved</div>
  </footer>
</body>
</html>
```